Verodex business card

Business card for sustainable investment company called "Verodex". Verodex is an exchange platform selling carbon credits between buyers and sellers. Carbon Credits are an environmental commodity for reducing global carbon emissions.

the card should obviously have our logo and the theme should be sustainability/environment mixed with a trading platform.

Contact Information for Business Card

Logo, Name, Title, Phone, Email

Colors
0054AA
0677BA
7BADD7
CADEEF
E8F1F8
0094D4
00A9DD
6FCCEA
C7EBF8
E9F6FB
00AB8E
00BBA5
67D7C9
C6EFE9
E9F9F6
59FF00
82FF00
B8FF75
E3FFCB
F4FFEA

```html
<!DOCTYPE html>
<html lang="en">
<head>
<meta charset="utf-8">
<title>Verodex Business Card</title>
<link href="https://fonts.googleapis.com/css2?family=Montserrat:wght@400;500;600;700&family=Pinyon+Script&display=swap" rel="stylesheet">
<style>
  :root {
    --backdrop: #c5c6c8;
    --paper: #ecebe3;
    --ink: #151515;
    --navy: #0f2458;
    --edge: #1fa3c9;
    --accent: #3a95d4;
    --white: #f2f4f7;
  }
  * { margin: 0; padding: 0; box-sizing: border-box; }
  html, body {
    width: 1200px;
    height: 1050px;
    overflow: hidden;
    background: var(--backdrop);
  }
  .canvas {
    position: relative;
    width: 1200px;
    height: 1050px;
  }
  .card {
    position: absolute;
    width: 580px;
    height: 330px;
    border-radius: 4px;
    box-shadow: 0 18px 40px rgba(0,0,0,0.18);
  }
  .card--front {
    left: 70px;
    top: 580px;
    background: var(--paper);
    border-bottom: 4px solid var(--edge);
    text-align: center;
    color: var(--ink);
    font-family: "Montserrat", sans-serif;
    padding-top: 48px;
  }
  .card--back {
    left: 550px;
    top: 150px;
    background: var(--navy);
    border-bottom: 8px solid var(--edge);
    display: flex;
    align-items: center;
    justify-content: center;
  }
  .brand {
    font-family: "Montserrat", sans-serif;
    font-weight: 600;
    letter-spacing: 0.06em;
  }
  .card--front .brand {
    font-size: 26px;
    color: var(--ink);
  }
  .person-name {
    margin-top: 30px;
    font-size: 30px;
    font-weight: 700;
    letter-spacing: 0.12em;
  }
  .person-title {
    font-family: "Pinyon Script", cursive;
    font-size: 20px;
    margin-top: 2px;
  }
  .contact {
    margin-top: 18px;
    font-size: 15px;
    font-weight: 500;
    letter-spacing: 0.18em;
    line-height: 1.8;
  }
  .brand-lockup {
    display: flex;
    align-items: center;
    gap: 18px;
  }
  .brand-lockup__square {
    width: 34px;
    height: 34px;
    background: var(--accent);
  }
  .card--back .brand {
    font-size: 44px;
    color: var(--white);
  }
</style>
</head>
<body>
  <main class="canvas">
    <section class="card card--back" aria-label="Business card back">
      <div class="brand-lockup">
        <span class="brand-lockup__square"></span>
        <span class="brand">VERODEX</span>
      </div>
    </section>

    <section class="card card--front" aria-label="Business card front">
      <div class="brand">Verodex</div>
      <h1 class="person-name">DANIEL REED</h1>
      <p class="person-title">Founder</p>
      <p class="contact">
        WWW.VERODEX.COM | 555-210-4387<br>
        INFO@VERODEX.COM
      </p>
    </section>
  </main>
</body>
</html>
```